Looking for a modern, Professional business card design

We have a simple business card, but are looking for a more modern, professional look. A sample of the basic card is attached as well as the logo. We would also like to add that we offer:
Struggling with your finances?
- Learn to become debt free
- Discover the power of cash
- Control your money instead of it controlling you
Let us help you achieve a new level of financial freedom!
Also, we would like to have a "SPECIAL OFFER!: FREE 30 minute consultation"
Financial Planning

```html
<!DOCTYPE html>
<html lang="en">
<head>
<meta charset="utf-8">
<title>Clearpath Coaching – Business Card</title>
<link href="https://fonts.googleapis.com/css2?family=Open+Sans:ital,wght@0,400;0,600;0,700;0,800;1,400;1,700&display=swap" rel="stylesheet">
<style>
  :root {
    --stage: #e6e6e6;
    --card-white: #ffffff;
    --brand-green: #3f9a3a;
    --green-deep: #3b8f3a;
    --green-glow: #a8d03a;
    --ink: #1c1c1c;
    --ink-soft: #4a4a4a;
    --rule: #b9b9b9;
    --on-green: #ffffff;
  }
  * { box-sizing: border-box; margin: 0; padding: 0; }
  html, body {
    width: 1105px; height: 1200px; overflow: hidden;
    background: var(--stage);
    font-family: "Open Sans", Arial, sans-serif;
  }
  .canvas { position: relative; width: 1105px; height: 1200px; }

  .card {
    position: absolute; left: 193px; width: 718px; height: 411px;
  }
  .card--front { top: 181px; background: var(--card-white); }
  .card--back {
    top: 636px;
    background: radial-gradient(ellipse 55% 70% at 50% 42%, var(--green-glow) 0%, #7cbd3b 45%, var(--green-deep) 100%);
    color: var(--on-green);
    text-align: center;
  }

  /* Front */
  .brand {
    position: absolute; right: 40px; top: 78px;
    display: flex; align-items: center; gap: 12px;
  }
  .brand__dot { width: 26px; height: 26px; border-radius: 50%; background: var(--brand-green); }
  .brand__name {
    font-weight: 800; font-size: 31px; letter-spacing: 0.5px;
    color: var(--ink); text-transform: uppercase;
  }

  .identity {
    position: absolute; left: 41px; top: 268px;
    display: flex; align-items: baseline; gap: 12px;
  }
  .identity__name { font-size: 25px; font-weight: 600; color: var(--brand-green); }
  .identity__dash { font-size: 25px; font-weight: 600; color: var(--brand-green); }
  .identity__role { font-size: 19px; color: var(--ink); }

  .divider {
    position: absolute; left: 41px; right: 42px; top: 309px;
    border-top: 1px solid var(--rule);
  }

  .contacts {
    position: absolute; left: 41px; top: 320px;
    font-size: 19px; color: var(--ink-soft); line-height: 29px;
  }
  .contacts__row { display: flex; align-items: center; gap: 22px; }
  .contact { display: flex; align-items: center; gap: 8px; }
  .contact svg { width: 17px; height: 17px; fill: var(--brand-green); flex: none; }

  /* Back */
  .back-brand {
    position: absolute; left: 0; right: 0; top: 110px;
    display: flex; justify-content: center; align-items: center; gap: 14px;
  }
  .back-brand__dot { width: 30px; height: 30px; border-radius: 50%; background: var(--on-green); }
  .back-brand__name {
    font-weight: 800; font-size: 36px; letter-spacing: 0.5px;
    text-transform: uppercase; color: var(--on-green);
  }

  .pitch { position: absolute; left: 0; right: 0; top: 240px; }
  .pitch__title { font-size: 21px; font-weight: 700; letter-spacing: 0.2px; line-height: 28px; }
  .pitch__line { font-size: 19px; font-style: italic; line-height: 26.5px; }
  .pitch__offer {
    margin-top: 10px;
    font-size: 27px; font-weight: 700; font-style: italic;
  }
</style>
</head>
<body>
<main class="canvas">

  <section class="card card--front" aria-label="Business card front">
    <div class="brand">
      <span class="brand__dot"></span>
      <span class="brand__name">Clearpath Coaching</span>
    </div>

    <div class="identity">
      <span class="identity__name">Daniel R. Hale</span>
      <span class="identity__dash">-</span>
      <span class="identity__role">Personal Financial Coach</span>
    </div>
    <div class="divider"></div>

    <div class="contacts">
      <div class="contacts__row">
        <span class="contact">
          <svg viewBox="0 0 16 16" aria-hidden="true"><path d="M4 0h8a1.5 1.5 0 0 1 1.5 1.5v13A1.5 1.5 0 0 1 12 16H4a1.5 1.5 0 0 1-1.5-1.5v-13A1.5 1.5 0 0 1 4 0zm0.5 2v10.5h7V2zm3.5 11.2a0.9 0.9 0 1 0 0 1.8a0.9 0.9 0 0 0 0-1.8z"/></svg>
          (555) 014-2278
        </span>
        <span class="contact">
          <svg viewBox="0 0 16 16" aria-hidden="true"><path d="M1 3h14v1.2L8 9 1 4.2zM1 5.6l7 4.8 7-4.8V13H1z"/></svg>
          daniel@clearpathmoney.com
        </span>
      </div>
      <div class="contacts__row">
        <span class="contact">
          <svg viewBox="0 0 16 16" aria-hidden="true"><path d="M8 0a8 8 0 1 0 0 16A8 8 0 0 0 8 0zm-1 2.2c-.8.9-1.6 1.5-1.4 2.6.2.9 1.6.8 1.9 1.7.3 1-.9 1.6-.6 2.7.3 1 1.5 1.2 1.5 2.5 0 .9-.5 1.6-.6 2.2A6 6 0 0 1 2.3 6c.9-.2 1.5.4 2.1.9.2-1.6 1.2-3.6 2.6-4.7zm4.2 1.2A6 6 0 0 1 14 8c-.6.2-1.4-.2-1.9.5-.6.9.3 2-.6 2.8-.7.6-1.6.1-1.8-.8-.2-1.1.9-1.9.4-3-.5-1-1.8-.8-2-1.8-.1-.8 1.4-1.6 3.1-2.3z"/></svg>
          www.clearpathmoney.com
        </span>
      </div>
    </div>
  </section>

  <section class="card card--back" aria-label="Business card back">
    <div class="back-brand">
      <span class="back-brand__dot"></span>
      <span class="back-brand__name">Clearpath Coaching</span>
    </div>

    <div class="pitch">
      <p class="pitch__title">STRUGGLING WITH YOUR FINANCES?</p>
      <p class="pitch__line">Learn to become debt free &bull; Discover the power of cash</p>
      <p class="pitch__line">Control your money instead of it controlling you</p>
      <p class="pitch__line">Let us help you achieve a new level of financial freedom!</p>
      <p class="pitch__offer">SPECIAL OFFER!: FREE 30 minute consultation</p>
    </div>
  </section>

</main>
</body>
</html>
```